Business card design for a dynamic IT consulting company

We need a business card design for a young firm, specialized in the Telecommunications/Consulting industry. The name of the company is Quindor and Partners Business Consulting Ltd. (Short name: Quindor and Partnes)
Quindor = solve read reverse, so we aim to be uncomplicated and solution-oriented. The small pipe in our logo is also related to the word solve. So we need a new business card design, which is simple, eye catching and something non traditional (I would probably prefer a square shaped design rather than a rectangle, but open for suggestions). Attached our logo.

Target Market(s)

Usually our customers are Tier1 Telecoms providers (Q-Netra, Palorix, etc) and their executives.

Industry/Entity Type

Business

Contact Information for Business Card

Name: Bence Tolnavari
Email: b.tolnavari@quindor.hu
Web: www.quindor.hu
Mobile: +36 30 518 2769
Title: Managing Director

Optional:
Company name: Quindor and Partners Ltd.
Address: 1087 Budapest, Tolvenka str. 28/C, Hungary

Font styles to use
Other font styles liked:
• helveticaneue_medium, Prime Regular are used now.

Colors

Designer to choose colors to be used in the design.

Requirements
Must have
• I would like to have a 2 sided design.
Nice to have
• I thought if we make the logo a bit bigger (without the company name), that could go to the back with the company name below. I though, if the pipe in the logo is somehow touchable on the business card, would be nice and unique.

```html
<!DOCTYPE html>
<html lang="en">
<head>
<meta charset="utf-8">
<title>Quindor and Partners – Business Card</title>
<link rel="stylesheet" href="https://fonts.googleapis.com/css2?family=Arimo:wght@400;700&display=swap">
<style>
  :root {
    --backdrop: #584535;
    --card: #f5f5f4;
    --blue: #0a93d3;
    --magenta: #b4338f;
    --grey: #5b5b5b;
    --text: #4d4d4d;
  }
  * { margin: 0; padding: 0; box-sizing: border-box; }
  html, body { width: 1200px; height: 960px; overflow: hidden; }
  body {
    background: var(--backdrop);
    position: relative;
    font-family: "Arimo", Arial, sans-serif;
    color: var(--text);
  }
  .card {
    position: absolute;
    top: 309px;
    width: 342px;
    height: 343px;
    background: var(--card);
    box-shadow: 2px 3px 4px rgba(0,0,0,0.35);
    overflow: hidden;
  }
  .card--front { left: 235px; }
  .card--back { left: 623px; text-align: center; }

  .pattern-area { position: absolute; top: 0; left: 0; }

  .holder-name {
    position: absolute; left: 42px; top: 150px;
    font-size: 17.5px; font-weight: 700; color: var(--blue);
    letter-spacing: 0.2px;
  }
  .holder-title {
    position: absolute; left: 42px; top: 175px;
    font-size: 14.5px; font-weight: 400; color: var(--text); letter-spacing: 0.3px;
  }
  .company-address {
    position: absolute; left: 42px; top: 205px;
    font-size: 13.5px; line-height: 18.5px; color: var(--text); font-style: normal;
  }
  .contact-list {
    position: absolute; left: 42px; top: 271px;
    list-style: none; font-size: 13.5px; line-height: 18.5px;
  }
  .contact-list li { display: flex; align-items: center; gap: 7px; }
  .contact-list svg { width: 12px; height: 12px; flex: none; }

  .brand-name {
    position: absolute; left: 0; right: 0; top: 190px;
    font-size: 25px; font-weight: 400; color: var(--grey);
    letter-spacing: 0.4px; line-height: 30px;
  }
  .brand-tagline {
    position: absolute; left: 0; right: 0; top: 219px;
    font-size: 8px; font-weight: 700; color: var(--grey);
    letter-spacing: 4.6px;
  }
  .brand-web {
    position: absolute; left: 0; right: 0; top: 293px;
    font-size: 13px; color: var(--text); letter-spacing: 8.5px;
  }
</style>
</head>
<body>
  <section class="card card--front">
    <svg class="pattern-area" width="342" height="343" viewBox="0 0 342 343"
         role="img" aria-label="Decorative pattern of small coloured squares along the top and right edges">
      <defs>
        <linearGradient id="edgeTone" x1="0" y1="0" x2="1" y2="1">
          <stop offset="0" stop-color="#b4338f" stop-opacity="0.35"/>
          <stop offset="0.5" stop-color="#0a93d3" stop-opacity="0.3"/>
          <stop offset="1" stop-color="#b4338f" stop-opacity="0.35"/>
        </linearGradient>
        <linearGradient id="innerTone" x1="0" y1="0" x2="1" y2="1">
          <stop offset="0" stop-color="#b4338f" stop-opacity="0.08"/>
          <stop offset="1" stop-color="#0a93d3" stop-opacity="0.1"/>
        </linearGradient>
      </defs>
      <rect x="60" y="45" width="240" height="230" fill="url(#innerTone)"/>
      <rect x="0" y="0" width="342" height="18" fill="url(#edgeTone)"/>
      <rect x="323" y="0" width="19" height="320" fill="url(#edgeTone)"/>
    </svg>

    <h1 class="holder-name">BENCE TOLNAVARI</h1>
    <p class="holder-title">MANAGING DIRECTOR</p>
    <address class="company-address">
      Quindor and Partners Ltd.<br>
      1087 Budapest<br>
      Tolvenka str. 28/C, Hungary
    </address>
    <ul class="contact-list">
      <li>
        <svg viewBox="0 0 12 12" aria-hidden="true"><rect x="3" y="0.5" width="6" height="11" rx="1" fill="none" stroke="#0a93d3" stroke-width="1.3"/><rect x="4.5" y="9" width="3" height="1" fill="#0a93d3"/></svg>
        +36 30 518 2769
      </li>
      <li>
        <svg viewBox="0 0 12 12" aria-hidden="true"><rect x="0.5" y="2.5" width="11" height="7" fill="#0a93d3"/><path d="M0.5 2.5 L6 6.5 L11.5 2.5" fill="none" stroke="#f5f5f4" stroke-width="1"/></svg>
        b.tolnavari@quindor.hu
      </li>
    </ul>
  </section>

  <section class="card card--back">
    <h2 class="brand-name">Quindor &amp; Partners</h2>
    <p class="brand-tagline">CLARITY · FOCUS · DRIVE</p>
    <p class="brand-web">www.quindor.hu</p>
  </section>
</body>
</html>
```